Floravine Pte Ltd

I want a creative and stand out web page so when my client search for my web page or google search. The front page is stand out and they know that we are the interior office designer that are searching for . We are commercial office design company. We also have the video to put at our front page for client to see. Natural is the key elements. As we like to carry recycle materials , plant , trees is our key element such as biophilic design
Updates

Hi All,

For my web page, I need minimalist design and creative frontpage.
When my client search for my web page, they straight feel that this is the office design company.
The webpage is special and nature is the key element for the design.
My company logo can be design in the shaped of the letter OO in the webpage.
Below is the sample you can refer.

https://www.pinboardly.example/pin/527190364821057392/

Target Market(s)

Customer searching for office design

Industry/Entity Type

Commerical designer firm- Office interior design & Build company

Number of Pages Required

5+ page

Font styles to use
Other font styles liked:
• Wilmina

Colors
59FF00
82FF00
B8FF75
E3FFCB
F4FFEA
FFC000
F8CF3A
FAE287
FDF2CF
FEFAEE
6B429C
8869AF
B7A5CE
E3DAEB
F3F0F8

Requirements
Must have
• Home, Services,Gallery, Calculator, Testimonials, Contact, Blog
Nice to have
• Natural, creative, minimalist
Should not have
• No black color or blue color

```html
<!DOCTYPE html>
<html lang="en">
<head>
<meta charset="utf-8">
<title>Floravine Pte Ltd — Office Interior Design</title>
<link href="https://fonts.googleapis.com/css2?family=Poppins:wght@300;400;500;600;700&display=swap" rel="stylesheet">
<style>
:root{
  --green:#59FF00;
  --green-2:#82FF00;
  --green-leaf:#4caf2a;
  --mint:#E3FFCB;
  --mint-soft:#F4FFEA;
  --gold:#FFC000;
  --gold-soft:#d9a94a;
  --purple:#6B429C;
  --accent:#F0431F;
  --ink:#2b2b2b;
  --text:#3d3d3d;
  --footer:#2f2f2f;
  --footer-bar:#262626;
  --paper:#ffffff;
  --mist:#f6f7f6;
}
*{box-sizing:border-box;margin:0;padding:0}
html,body{width:1200px;height:4269px;overflow:hidden}
body{font-family:"Poppins",sans-serif;color:var(--text);background:var(--paper);position:relative}
a{color:inherit;text-decoration:none}

/* header */
.site-header{position:absolute;left:0;top:0;width:1200px;height:78px;background:var(--paper)}
.brand{position:absolute;left:106px;top:20px;display:flex;align-items:center;gap:10px}
.brand-dot{width:34px;height:34px;border-radius:50%;background:var(--green-leaf)}
.brand-name{font-weight:600;font-size:20px;color:var(--green-leaf);line-height:1}
.main-nav a{position:absolute;top:27px;font-size:15px;font-weight:600;color:var(--ink)}
.main-nav a.active{color:var(--accent)}

/* hero */
.hero{position:absolute;left:0;top:78px;width:1200px;height:522px;
  background:linear-gradient(180deg,#3f4a3c 0%,#55664a 45%,#2f4a22 100%)}
.hero-title{position:absolute;left:0;top:133px;width:1200px;text-align:center;color:#fff;
  font-weight:400;font-size:29px;line-height:57px;text-transform:uppercase;letter-spacing:.2px}
.play{position:absolute;left:578px;top:334px;width:44px;height:44px}
.hero-social{position:absolute;left:1134px;width:16px;height:16px;border-radius:50%;background:#fff}

/* foliage areas */
.foliage{position:absolute;background:linear-gradient(135deg,rgba(143,209,79,.55),rgba(63,143,34,.35))}

/* about */
.section-title{position:absolute;color:var(--purple);font-weight:400;font-size:34px;text-transform:uppercase;letter-spacing:.3px;line-height:1}
.about-copy{position:absolute;left:111px;top:760px;width:490px;font-size:17px;line-height:32.5px;color:var(--text)}
.about-copy p+p{margin-top:22px}
.btn-read{position:absolute;left:111px;top:1118px;width:133px;height:40px;background:var(--green-2);
  color:var(--purple);font-weight:700;font-size:14px;display:flex;align-items:center;justify-content:center}
.about-photo{position:absolute;left:757px;top:693px;width:332px;height:465px;
  background:linear-gradient(160deg,#4f5a3a 0%,#8a7a55 40%,#c9a468 60%,#3d4a30 100%)}
.dots{position:absolute;background-image:radial-gradient(circle,#8be05a 1.7px,transparent 2px);background-size:24px 24px}

/* awards */
.awards{position:absolute;left:0;top:1274px;width:1200px;height:471px;background:var(--mint-soft)}
.arrow{position:absolute;width:14px;height:20px}
.award{position:absolute;top:1466px;width:130px;height:145px;display:flex;align-items:center;justify-content:center}
.award span{display:block;border-radius:50%;border:8px solid var(--gold-soft)}

/* services */
.services-copy{position:absolute;left:104px;top:1975px;width:314px;text-align:center;font-size:15px;line-height:30px;color:var(--text)}
.card{position:absolute;width:303px;height:374px;background:var(--paper);box-shadow:0 2px 14px rgba(0,0,0,.08)}
.card.featured{background:var(--mint-soft)}
.card-media{position:absolute;left:13px;top:13px;width:277px;height:123px}
.card-title{position:absolute;left:0;top:163px;width:100%;text-align:center;font-size:14px;font-weight:400;text-transform:uppercase;color:var(--ink)}
.card-body{position:absolute;left:22px;top:200px;width:259px;text-align:center;font-size:15px;line-height:30px;color:var(--text)}
.featured .card-body{top:190px}
.learn{position:absolute;left:0;top:325px;width:100%;text-align:center;font-size:14px;font-weight:600;color:var(--purple);text-decoration:underline}

/* portfolio */
.portfolio{position:absolute;left:0;top:2784px;width:1200px;height:613px;
  background:linear-gradient(180deg,#eef7e2,#f3faea)}
.work{position:absolute;top:2958px;width:482px;height:296px}
.work-name{position:absolute;top:3276px;width:482px;text-align:center;font-size:17px;font-weight:600;color:var(--ink);text-transform:uppercase}

/* partners */
.partners{position:absolute;left:0;top:3397px;width:1200px;height:489px;background:var(--mist)}
.partner{position:absolute;top:3638px;width:124px;height:124px;display:flex;align-items:center;justify-content:center}

/* footer */
.site-footer{position:absolute;left:0;top:3886px;width:1200px;height:308px;background:var(--footer)}
.footer-brand{position:absolute;left:0;top:3984px;width:1200px;display:flex;align-items:center;justify-content:center;gap:10px}
.footer-nav a{position:absolute;top:4058px;font-size:15px;font-weight:600;color:#fff}
.foot-social{position:absolute;top:4115px;width:16px;height:16px;border-radius:50%;background:#fff}
.chat{position:absolute;left:1082px;top:3950px;width:54px;height:54px;border-radius:50%;background:#fff}
.footer-bar{position:absolute;left:0;top:4194px;width:1200px;height:75px;background:var(--footer-bar);color:#fff;font-size:15px}
.footer-bar .copy{position:absolute;left:108px;top:27px}
.footer-bar .code{position:absolute;left:1049px;top:27px}
</style>
</head>
<body>

<header class="site-header">
  <div class="brand"><span class="brand-dot"></span><span class="brand-name">Floravine Pte Ltd</span></div>
  <nav class="main-nav">
    <a class="active" style="left:336px">Home</a>
    <a style="left:415px">Services</a>
    <a style="left:515px">Gallery</a>
    <a style="left:605px">Calculator</a>
    <a style="left:722px">Testimonials</a>
    <a style="left:857px">Contact</a>
    <a style="left:955px">Blog</a>
    <a style="left:1022px">Portfolio</a>
  </nav>
</header>

<section class="hero" role="img" aria-label="Video still of a glass office tower surrounded by trees and greenery">
  <h1 class="hero-title">Bring goods straight from<br>factory &amp; cut away the middleman costing so client can<br>have a better quality with affordable price.</h1>
  <svg class="play" viewBox="0 0 44 44" aria-label="Play video"><circle cx="22" cy="22" r="20" fill="none" stroke="#fff" stroke-width="2"/><path d="M18 14 L30 22 L18 30 Z" fill="none" stroke="#fff" stroke-width="2" stroke-linejoin="round"/></svg>
  <span class="hero-social" style="top:381px"></span>
  <span class="hero-social" style="top:414px"></span>
  <span class="hero-social" style="top:449px"></span>
</section>

<!-- about -->
<div class="foliage" role="img" aria-label="Cluster of green leaves at the top right corner" style="left:995px;top:600px;width:205px;height:200px"></div>
<div class="foliage" role="img" aria-label="Cluster of green leaves at the bottom left corner" style="left:0;top:1040px;width:175px;height:234px"></div>

<h2 class="section-title" style="left:107px;top:690px">About Floravine</h2>
<div class="about-copy">
  <p>Floravine is an interior design and renovation company that specialises in office interior design and commercial retail renovation. We always aim to provide premium quality services with competitive cost and ensuring our clients are pleased with the outcome.</p>
  <p>Since 2010 when the firm began, Floravine has amassed a wealth of experience in commercial interior design. Our team of dedicated and professional designers is committed to creating</p>
</div>
<a class="btn-read">READ MORE</a>
<div class="dots" style="left:668px;top:760px;width:60px;height:330px"></div>
<div class="dots" style="left:1092px;top:800px;width:80px;height:290px"></div>
<div class="about-photo" role="img" aria-label="Photo of a biophilic open-plan office with hanging plants and timber stairs"></div>

<!-- awards -->
<section class="awards">
  <h2 class="section-title" style="left:0;width:1200px;text-align:center;top:92px">Awards</h2>
</section>
<svg class="arrow" style="left:155px;top:1528px" viewBox="0 0 14 20"><path d="M11 3 L4 10 L11 17" fill="none" stroke="var(--ink)" stroke-width="3"/></svg>
<svg class="arrow" style="left:1031px;top:1528px" viewBox="0 0 14 20"><path d="M3 3 L10 10 L3 17" fill="none" stroke="var(--ink)" stroke-width="3"/></svg>
<div class="award" style="left:227px"><span style="width:120px;height:120px"></span></div>
<div class="award" style="left:439px"><span style="width:110px;height:110px;border-color:#c9a05a"></span></div>
<div class="award" style="left:644px"><span style="width:110px;height:110px;border-color:#b8955a"></span></div>
<div class="award" style="left:846px"><span style="width:110px;height:110px;border-color:var(--gold)"></span></div>

<!-- services -->
<h2 class="section-title" style="left:138px;top:1911px">Our Services</h2>
<p class="services-copy">For Floravine, design has no limit and value. We constantly strive to make sure that our clients get the best services possible. We offer our services to corporate and commercial industries including food and beverage, retail, education, government and hospitality to name a few.</p>

<article class="card" style="left:446px;top:1876px">
  <div class="card-media" role="img" aria-label="Photo of a walkway lined with green vertical plant walls" style="background:linear-gradient(135deg,#8fbf5a,#3f7a2a 60%,#a6b4a0)"></div>
  <h3 class="card-title">Pre-Lease Service</h3>
  <p class="card-body">It can be rather tedious and challenging to find the perfect office space that will suit your unique needs and concerns.</p>
</article>

<article class="card featured" style="left:780px;top:1876px">
  <div class="card-media" role="img" aria-label="Photo of a bright office lounge with arched windows and plants" style="background:linear-gradient(135deg,#6a7a55,#a89a78 50%,#5f7a40)"></div>
  <h3 class="card-title">Interior Design &amp; Planning</h3>
  <p class="card-body">We understand the importance of having a conducive environment to support your company's day-to-day operations.</p>
  <a class="learn">LEARN MORE</a>
</article>

<article class="card" style="left:108px;top:2297px">
  <div class="card-media" role="img" aria-label="Photo of an indoor garden atrium with columns" style="background:linear-gradient(135deg,#4a4f46,#8c9a80 50%,#3a4336)"></div>
  <h3 class="card-title">Engineering Services</h3>
  <p class="card-body">Our company can design electrical and mechanical systems, which work seamlessly with building provisions that ad-</p>
</article>

<article class="card" style="left:446px;top:2297px">
  <div class="card-media" role="img" aria-label="Photo of desks in front of a green moss wall" style="background:linear-gradient(135deg,#5c7a3a,#8fa86a 50%,#d8d2c4)"></div>
  <h3 class="card-title">Procurement &amp; Construction</h3>
  <p class="card-body">Another part of our services include the procurement and construction. We understand how complicated it can be to</p>
</article>

<article class="card" style="left:780px;top:2297px">
  <div class="card-media" role="img" aria-label="Photo of a meeting room with timber panels and a living wall" style="background:linear-gradient(135deg,#3e4a38,#6e8a4a 45%,#8a6a48)"></div>
  <h3 class="card-title">Migration Management</h3>
  <p class="card-body">We realize the importance of continuous checks on your project even long after its construction. Hence, you can count</p>
</article>

<!-- portfolio -->
<section class="portfolio">
  <h2 class="section-title" style="left:0;width:1200px;text-align:center;top:87px">Portfolio</h2>
</section>
<div class="work" role="img" aria-label="Photo of a reception counter with a golden quilted wall" style="left:-171px;background:linear-gradient(120deg,#e8dcc8 0%,#c8922e 45%,#e0b64a 70%,#8a5a1a)"></div>
<div class="work-name" style="left:-171px">Solvara Inti Holdings</div>
<div class="work" role="img" aria-label="Photo of a restaurant interior with brick walls and wooden tables" style="left:360px;background:linear-gradient(120deg,#8a4a2a,#5a3a28 40%,#c8a070 60%,#4a3020)"></div>
<div class="work-name" style="left:360px">Basil Lane Kitchen</div>
<div class="work" role="img" aria-label="Photo of a white showroom with display stands" style="left:890px;background:linear-gradient(120deg,#f2f2f4,#d8dade 50%,#bfc4cc)"></div>
<div class="work-name" style="left:890px">Meridion Asia Pacific</div>

<!-- partners -->
<section class="partners">
  <h2 class="section-title" style="left:0;width:1200px;text-align:center;top:112px">Our Partnets</h2>
</section>
<svg class="arrow" style="left:160px;top:3690px" viewBox="0 0 14 20"><path d="M11 3 L4 10 L11 17" fill="none" stroke="var(--ink)" stroke-width="3"/></svg>
<svg class="arrow" style="left:1036px;top:3690px" viewBox="0 0 14 20"><path d="M3 3 L10 10 L3 17" fill="none" stroke="var(--ink)" stroke-width="3"/></svg>
<div class="partner" style="left:254px"><svg width="124" height="124"><circle cx="62" cy="62" r="58" fill="#38484a"/></svg></div>
<div class="partner" style="left:462px"><svg width="124" height="124"><circle cx="62" cy="62" r="50" fill="#8cc63f"/></svg></div>
<div class="partner" style="left:657px"><svg width="124" height="124"><rect x="16" y="16" width="92" height="92" fill="#c4d82e"/></svg></div>
<div class="partner" style="left:838px"><svg width="124" height="124"><rect x="18" y="18" width="88" height="88" fill="#f47a20"/></svg></div>

<!-- footer -->
<footer class="site-footer"></footer>
<div class="footer-brand"><span class="brand-dot"></span><span class="brand-name" style="font-size:24px">Floravine Pte Ltd</span></div>
<nav class="footer-nav">
  <a style="left:225px">Home</a>
  <a style="left:305px">Services</a>
  <a style="left:405px">Gallery</a>
  <a style="left:494px">Calculator</a>
  <a style="left:611px">Testimonials</a>
  <a style="left:747px">Contact</a>
  <a style="left:844px">Blog</a>
  <a style="left:911px">Portfolio</a>
</nav>
<span class="foot-social" style="left:509px"></span>
<span class="foot-social" style="left:545px"></span>
<span class="foot-social" style="left:580px"></span>
<span class="foot-social" style="left:627px"></span>
<span class="foot-social" style="left:679px"></span>
<div class="chat"><svg width="54" height="54" viewBox="0 0 54 54"><circle cx="17" cy="27" r="4" fill="var(--footer)"/><circle cx="27" cy="27" r="4" fill="var(--footer)"/><circle cx="37" cy="27" r="4" fill="var(--footer)"/></svg></div>
<div class="footer-bar">
  <span class="copy">© 2023 floravine pte ltd</span>
  <span class="code">C64</span>
</div>

</body>
</html>
```